KESTREL Academy Exhibit Booth Posters

My company is KESTREL Academy (a division of KESTREL for Growth). We are exhibiting in a month, and I need to re-do my exhibit booth posters. There will be a total of 4 posters needed. Sizes are below.
1) Top- 11 feet long X 12 inches wide (Try to match color scheme in example photo)
2) Center- 4 feet long X 2 feet wide (Chalkboard background)
3) Left- 18 inches long X 2 feet wide (Cork-board back ground with the use of push pins holding up post-it-notes, paper, etc.)
4) Right- 18 inches long X 2 feet wide (Cork-board back ground with the use of push pins holding up post-it-notes, paper, etc.)
I have attached a photo of my old booth. This will get you an idea of the size, color schemes, and more. I have created basic rendering of each poster. The content is important, but the look and design should be drastically improved.
The websites to look into for ideas are:
www.kestrelforgrowth.example
www.kestrelacademy.example
Updates
I've added a new file. It's a .JPG of the certification diploma. Thanks!
Target Market(s)
Business Owners, Managers, HR, Supervisors, Teens who want to boost their resume
Industry/Entity Type
It Company
Look and feel

```html
<!DOCTYPE html>
<html lang="en">
<head>
<meta charset="utf-8">
<title>KESTREL Academy – Booth Side Poster</title>
<link rel="stylesheet" href="https://fonts.googleapis.com/css2?family=Oswald:wght@600;700&family=Roboto+Condensed:ital,wght@0,700;1,700&display=swap">
<style>
  :root {
    --page: #ffffff;
    --frame-dark: #9a5a1c;
    --frame-mid: #d08a3c;
    --frame-light: #e9b26a;
    --cork: #b98a56;
    --cork-light: #cfa36e;
    --cork-dark: #9c6f3f;
    --title-paper-a: #fde6bf;
    --title-paper-b: #f6d9c9;
    --paper: #ffffff;
    --paper-shade: #e7e7e7;
    --tape: #f4f4f1;
    --red: #e3161f;
    --red-shadow: #8a8a8a;
    --pin-red: #d41f24;
    --pin-blue: #2866c4;
    --pin-grey: #555a60;
    --sticky: #fbf59a;
    --sticky-edge: #e7df74;
    --ink-blue: #1f3f8f;
    --tick-green: #2d8a2d;
    --book-blue: #3a7fc1;
    --book-red: #c5262d;
  }
  html, body {
    margin: 0;
    padding: 0;
    width: 1004px;
    height: 1200px;
    overflow: hidden;
    background: var(--page);
  }
  .poster { display: block; width: 1004px; height: 1200px; }
  .title-text {
    font-family: "Roboto Condensed", "Arial Narrow", sans-serif;
    font-style: italic;
    font-weight: 700;
    font-size: 63px;
    fill: var(--red);
  }
  .bullet-text {
    font-family: "Oswald", "Arial Narrow", sans-serif;
    font-weight: 700;
    font-size: 52px;
    fill: var(--red);
  }
  .bullet-shadow { fill: var(--red-shadow); opacity: .55; }
  .note-lead {
    font-family: "Roboto Condensed", "Arial Narrow", sans-serif;
    font-weight: 700;
    font-size: 44px;
    fill: var(--red);
  }
  .note-item, .note-ask {
    font-family: "Roboto Condensed", "Arial Narrow", sans-serif;
    font-weight: 700;
    font-size: 33px;
    fill: var(--ink-blue);
  }
  .tick { fill: var(--tick-green); }
</style>
</head>
<body>
<svg class="poster" viewBox="0 0 1004 1200" xmlns="http://www.w3.org/2000/svg">
  <defs>
    <linearGradient id="frameGrad" x1="0" y1="0" x2="1" y2="1">
      <stop offset="0" stop-color="var(--frame-light)"/>
      <stop offset=".5" stop-color="var(--frame-mid)"/>
      <stop offset="1" stop-color="var(--frame-dark)"/>
    </linearGradient>
    <radialGradient id="corkGrad" cx=".5" cy=".45" r=".75">
      <stop offset="0" stop-color="var(--cork-light)"/>
      <stop offset=".7" stop-color="var(--cork)"/>
      <stop offset="1" stop-color="var(--cork-dark)"/>
    </radialGradient>
    <filter id="corkTexture" x="0" y="0" width="100%" height="100%">
      <feTurbulence type="fractalNoise" baseFrequency="0.11" numOctaves="3" seed="4" result="noise"/>
      <feColorMatrix in="noise" type="matrix" values="0 0 0 0 0.42  0 0 0 0 0.26  0 0 0 0 0.10  3.2 0 0 0 -1.55" result="dark"/>
      <feColorMatrix in="noise" type="matrix" values="0 0 0 0 0.93  0 0 0 0 0.76  0 0 0 0 0.52  0 3.2 0 0 -1.6" result="light"/>
      <feComposite in="dark" in2="SourceGraphic" operator="in" result="darkIn"/>
      <feComposite in="light" in2="SourceGraphic" operator="in" result="lightIn"/>
      <feMerge>
        <feMergeNode in="SourceGraphic"/>
        <feMergeNode in="darkIn"/>
        <feMergeNode in="lightIn"/>
      </feMerge>
    </filter>
    <linearGradient id="titlePaperGrad" x1="0" y1="0" x2="1" y2="1">
      <stop offset="0" stop-color="var(--title-paper-b)"/>
      <stop offset=".5" stop-color="var(--title-paper-a)"/>
      <stop offset="1" stop-color="var(--title-paper-b)"/>
    </linearGradient>
    <linearGradient id="paperGrad" x1="0" y1="0" x2="1" y2="1">
      <stop offset="0" stop-color="var(--paper)"/>
      <stop offset=".85" stop-color="var(--paper)"/>
      <stop offset="1" stop-color="var(--paper-shade)"/>
    </linearGradient>
    <linearGradient id="bookGrad" x1="0" y1="0" x2="0" y2="1">
      <stop offset="0" stop-color="var(--book-blue)"/>
      <stop offset=".5" stop-color="var(--book-red)"/>
      <stop offset="1" stop-color="var(--book-red)"/>
    </linearGradient>
    <filter id="softShadow" x="-10%" y="-10%" width="130%" height="130%">
      <feDropShadow dx="4" dy="6" stdDeviation="5" flood-color="#000" flood-opacity=".3"/>
    </filter>
    <symbol id="pin" viewBox="-20 -20 40 40" overflow="visible">
      <ellipse cx="10" cy="16" rx="9" ry="5" fill="#000" opacity=".18"/>
      <rect x="-2" y="2" width="4" height="14" rx="2" fill="#c9c9c9"/>
      <circle cx="0" cy="0" r="13" fill="currentColor"/>
      <circle cx="-4" cy="-4" r="4" fill="#fff" opacity=".45"/>
    </symbol>
  </defs>

  <g class="board">
    <rect x="87" y="40" width="837" height="1110" fill="url(#frameGrad)"/>
    <rect x="104" y="57" width="803" height="1076" fill="url(#corkGrad)" filter="url(#corkTexture)" role="img" aria-label="Cork board surface"/>
  </g>

  <g class="title-card" filter="url(#softShadow)">
    <rect x="185" y="108" width="662" height="210" fill="url(#titlePaperGrad)"/>
  </g>
  <g class="tape">
    <rect x="226" y="112" width="46" height="30" fill="var(--tape)" opacity=".9" transform="rotate(-20 249 127)"/>
    <rect x="726" y="104" width="48" height="30" fill="var(--tape)" opacity=".9" transform="rotate(25 750 119)"/>
    <rect x="460" y="300" width="48" height="28" fill="var(--tape)" opacity=".9" transform="rotate(8 484 314)"/>
  </g>
  <use href="#pin" x="758" y="74" width="40" height="40" style="color: var(--pin-blue)"/>
  <text class="title-text" x="514" y="188" text-anchor="middle">Content Based on</text>
  <text class="title-text" x="512" y="260" text-anchor="middle">Employer Feedback</text>

  <polygon class="bullet-sheet" points="145,460 770,333 857,808 248,922" fill="url(#paperGrad)" filter="url(#softShadow)"/>
  <use href="#pin" x="698" y="336" width="40" height="40" style="color: var(--pin-red)"/>
  <use href="#pin" x="178" y="440" width="40" height="40" style="color: var(--pin-red)"/>

  <g class="bullets" transform="rotate(-13 214 575)">
    <g>
      <circle cx="196" cy="558" r="6" fill="var(--red)"/>
      <text class="bullet-text bullet-shadow" x="217" y="579">It’s More Than a Paychek</text>
      <text class="bullet-text" x="214" y="575">It’s More Than a Paychek</text>
    </g>
    <g transform="translate(4 89)">
      <circle cx="196" cy="558" r="6" fill="var(--red)"/>
      <text class="bullet-text bullet-shadow" x="217" y="579">It’s All About Attitude</text>
      <text class="bullet-text" x="214" y="575">It’s All About Attitude</text>
    </g>
    <g transform="translate(10 178)">
      <circle cx="196" cy="558" r="6" fill="var(--red)"/>
      <text class="bullet-text bullet-shadow" x="217" y="579">Play By The Rules</text>
      <text class="bullet-text" x="214" y="575">Play By The Rules</text>
    </g>
    <g transform="translate(14 267)">
      <circle cx="196" cy="558" r="6" fill="var(--red)"/>
      <text class="bullet-text bullet-shadow" x="217" y="579">And Much More</text>
      <text class="bullet-text" x="214" y="575">And Much More</text>
    </g>
  </g>

  <rect class="books" x="664" y="716" width="156" height="62" rx="8" fill="url(#bookGrad)" transform="rotate(-4 742 747)" role="img" aria-label="Illustration of a small stack of books with a pencil"/>

  <g class="sticky sticky-be" transform="rotate(-2 476 1010)">
    <rect x="388" y="912" width="176" height="196" fill="var(--sticky)" filter="url(#softShadow)"/>
    <rect x="388" y="912" width="176" height="6" fill="var(--sticky-edge)"/>
    <text class="note-lead" x="402" y="962">Be...</text>
    <path class="tick" d="M414 980 l4 8 9 -2 -7 6 4 9 -8 -5 -8 5 4 -9 -7 -6 9 2z"/>
    <text class="note-item" x="432" y="998">There</text>
    <path class="tick" d="M414 1020 l4 8 9 -2 -7 6 4 9 -8 -5 -8 5 4 -9 -7 -6 9 2z"/>
    <text class="note-item" x="432" y="1038">On Time</text>
    <path class="tick" d="M414 1060 l4 8 9 -2 -7 6 4 9 -8 -5 -8 5 4 -9 -7 -6 9 2z"/>
    <text class="note-item" x="432" y="1078">Focused</text>
  </g>
  <use href="#pin" x="492" y="894" width="40" height="40" style="color: var(--pin-grey)"/>

  <g class="sticky sticky-ask" transform="rotate(9 764 984)">
    <rect x="660" y="872" width="208" height="222" fill="var(--sticky)" filter="url(#softShadow)"/>
    <rect x="660" y="872" width="208" height="6" fill="var(--sticky-edge)"/>
    <text class="note-ask" x="764" y="944" text-anchor="middle">Ask Us</text>
    <text class="note-ask" x="764" y="988" text-anchor="middle">About A</text>
    <text class="note-ask" x="764" y="1032" text-anchor="middle">Sneak Peek</text>
  </g>
  <use href="#pin" x="764" y="868" width="40" height="40" style="color: var(--pin-grey)"/>
</svg>
</body>
</html>
```